Email Marketing Campaign Brief

We want to do an email marketing campaign around our consulting services. The attached documents provide back ground on our work but additional copy can be found below:

KV7lr is committed to helping you, the educator, make informed buying decisions based on local control and independent reviews through a simple, impartial and an effective approach.
In education, there exists a vast array of educational solutions – such as reading, science, language arts, and math curricula; school-wide reform programs; interventions; after-school programs; and new educational technologies. In the marketplace, providers could, and most do, claim to be able to improve educational outcomes and, in many cases, they all pretend to be supported by evidence. But a cursory review reveals that most evidence consists of poorly designed or advocacy-driven studies with some providers having such inadequate research as could only be described as case studies.

So the problem for State and local education officials is that they must sort through a myriad of such claims to decide which solutions merit consideration for their schools and classrooms. One US official stated the problem saying “many of these practitioners have seen interventions (solutions), introduced with great fanfare as being able to produce dramatic gains, come and go over the years, yielding little in the way of positive and lasting change – a perception confirmed by the flat achievement results over the past 30 years in the Federal Survey of Scholastic Attainment long-term trend”

KV7lr is a process by which we make you, the educator, the locus of control

OUR Approach:
With four simple, yet highly effective steps, KV7lr guides educators through an informed buying process that’s based on local control and review.

Step 1 — Research, Review, and Evaluation Criteria

Step 2 — Cost / Benefit Analysis

Step 3 — Education Survey & Culture Scan

Step 4 — Negotiation & Representation

Target Market(s)

Education

Industry/Entity Type

Marketing

Font styles to use
Sans Serif

Colors
f9b46a
f37122

Requirements
Must have
• HTML format that can be used in an Email Campaign
Nice to have
• Additional Copy in Word

```html
<!DOCTYPE html>
<html lang="en">
<head>
<meta charset="utf-8">
<title>KV7lr – Research, Policy, Practice</title>
<link href="https://fonts.googleapis.com/css2?family=Baloo+2:wght@800&family=PT+Sans:wght@400;700&family=Quicksand:wght@300;400&display=swap" rel="stylesheet">
<style>
  :root{
    --mint:#4af2c3;
    --brand-orange:#e8501c;
    --research:#ffa300;
    --policy:#d0353b;
    --practice:#17c1e6;
    --green:#25805e;
    --orange:#ea5220;
    --blue:#12a1df;
    --num-red:#e2414b;
    --ring:#f37122;
    --ink:#1e1e1e;
    --heading:#444;
    --white:#fff;
  }
  html,body{margin:0;padding:0;overflow:hidden;background:#fff;}
  .canvas{position:relative;width:1200px;height:1200px;overflow:hidden;background:var(--white);font-family:"PT Sans",sans-serif;color:var(--ink);}
  .abs{position:absolute;}
  .decor{left:0;top:0;}
  .nav-label{position:absolute;top:22px;font-family:"Baloo 2",sans-serif;font-weight:800;font-size:32px;color:var(--white);line-height:1;transform:translateX(-50%);}
  .brand{left:70px;top:82px;display:flex;align-items:center;gap:12px;font-family:"Quicksand",sans-serif;font-weight:400;font-size:50px;color:#fde3d4;line-height:1;}
  .brand-dot{width:14px;height:14px;border-radius:50%;background:#fde3d4;}
  .hero-text{left:0;width:1200px;text-align:center;font-family:"Baloo 2",sans-serif;font-weight:800;color:var(--white);text-shadow:0 2px 4px rgba(0,0,0,.45);line-height:1;}
  .hero-title{top:534px;font-size:45px;padding-left:30px;}
  .hero-sub{top:594px;font-size:31px;padding-left:30px;}
  .intro{top:682px;width:486px;font-size:12.2px;line-height:16px;text-align:justify;margin:0;}
  .intro p{margin:0;}
  .intro .gap{margin-top:16px;}
  .intro-left{left:95px;}
  .intro-right{left:614px;}
  .mark{color:var(--brand-orange);font-weight:700;}
  .approach-title{top:864px;left:0;width:1200px;text-align:center;font-family:"Baloo 2",sans-serif;font-weight:800;font-size:28px;color:var(--heading);line-height:1;}
  .approach-sub{top:893px;left:0;width:1200px;text-align:center;font-family:"Quicksand",sans-serif;font-weight:400;font-size:18.5px;line-height:22px;color:#333;}
  .step-num{width:84px;height:84px;border-radius:50%;background:var(--white);border:4px solid var(--ring);display:flex;align-items:center;justify-content:center;font-family:"Baloo 2",sans-serif;font-weight:800;font-size:58px;color:var(--num-red);line-height:1;padding-top:6px;box-sizing:content-box;}
  .step-title{text-align:center;font-family:"Quicksand",sans-serif;font-weight:400;font-size:28px;line-height:35px;color:var(--white);text-transform:uppercase;white-space:nowrap;letter-spacing:-0.2px;}
  .step-list{list-style:none;margin:0;padding:0;font-family:"Quicksand",sans-serif;font-weight:400;font-size:14px;color:var(--white);white-space:nowrap;}
  .step-list li{position:relative;padding-left:15px;line-height:19px;}
  .step-list li::before{content:"";position:absolute;left:0;top:4px;width:10px;height:10px;border-radius:50%;background:#f1f1f1;}
</style>
</head>
<body>
<div class="canvas">

  <svg class="abs decor" width="1200" height="1200" viewBox="0 0 1200 1200" aria-hidden="true">
    <path d="M0 0 H283 V45 H0 Z M0 180 H250 C235 230 200 270 160 300 C110 310 50 308 0 304 Z" fill="var(--mint)"/>
    <path d="M0 180 H250 L240 200 C210 250 175 280 140 300 L0 300 Z" fill="var(--mint)"/>
    <path d="M368 0 H688 L651 90 H402 Z" fill="var(--research)"/>
    <path d="M688 0 H961 L925 90 H651 Z" fill="var(--policy)"/>
    <path d="M961 0 H1200 V90 H925 Z" fill="var(--practice)"/>
  </svg>

  <svg class="abs" style="left:41px;top:130px" width="1118" height="525" viewBox="0 0 1118 525" role="img" aria-label="Photo of a smiling teacher and four children looking together at a tablet">
    <defs>
      <linearGradient id="heroTone" x1="0" y1="0" x2="1" y2="1">
        <stop offset="0" stop-color="#8a6a52"/>
        <stop offset=".45" stop-color="#d8b9a2"/>
        <stop offset=".75" stop-color="#e4cf6a"/>
        <stop offset="1" stop-color="#3f6fb8"/>
      </linearGradient>
    </defs>
    <path d="M0 0 H1118 V482 Q560 560 0 482 Z" fill="url(#heroTone)"/>
  </svg>

  <svg class="abs decor" width="1200" height="320" viewBox="0 0 1200 320" aria-hidden="true">
    <path d="M0 43 H370 L412 111 L372 179 H0 Z" fill="var(--brand-orange)"/>
    <path d="M250 179 H372 C340 220 290 260 250 280 C270 240 260 210 250 179 Z" fill="var(--white)"/>
  </svg>

  <div class="abs brand"><span class="brand-dot"></span>KV7lr</div>
  <span class="nav-label" style="left:509px">Research</span>
  <span class="nav-label" style="left:801px">Policy</span>
  <span class="nav-label" style="left:1069px">Practice</span>

  <div class="abs hero-text hero-title">We help you to build geniuses</div>
  <div class="abs hero-text hero-sub">Research, Teaching, Learning</div>

  <div class="abs intro intro-left">
    <p><span class="mark">KV7lr</span> is committed to helping you, the educator; make informed buying decisions based on local control and independent reviews through a simple, impartial and an effective approach.</p>
    <p>In education, there exists a vast array of educational solutions – such as reading, science, language arts, and math curricula; school-wide reform programs; interventions; after-school programs; and new educational technologies. In the marketplace, providers could, and most do, claim to be able to improve educational outcomes and, in many cases, they all pretend to be supported by evidence. But a cursory review reveals that most evidence consists of poorly designed or advocacy-driven studies with some providers having such inadequate research as could only be described as case studies.</p>
  </div>
  <div class="abs intro intro-right">
    <p>So the problem for State and local education officials is that they must sort through a myriad of such claims to decide which solutions merit consideration for their schools and classrooms.</p>
    <p>One US official stated the problem saying “many of these practitioners have seen interventions (solutions), introduced with great fanfare as being able to produce dramatic gains, come and go over the years, yielding little in the way of positive and lasting change – a perception confirmed by the flat achievement results over the past 30 years in the Federal Survey of Scholastic Attainment long-term trend”.</p>
    <p class="gap"><span class="mark">KV7lr</span> is a process by which we make you, the educator, the focus of control.</p>
  </div>

  <div class="abs approach-title">OUR Approach:</div>
  <div class="abs approach-sub">With four simple, yet highly effective steps, KV7lr guides educators through<br>an informed buying process that’s based on local control and review.</div>

  <svg class="abs decor" width="1200" height="1200" viewBox="0 0 1200 1200" aria-hidden="true">
    <path d="M26 1005 C30 975 60 955 95 955 C150 950 190 965 218 995 C240 975 270 965 310 972 C340 978 355 985 365 975 C380 968 395 975 398 1000 V1200 H20 Z" fill="var(--green)"/>
    <path d="M416 1022 L430 1019 L445 1023 L460 1017 L478 1021 L495 1016 L515 1022 L535 1018 L560 1024 L640 1022 L660 1018 L690 1023 L720 1017 L745 1022 L765 1018 L782 1021 V1200 H416 Z" fill="var(--orange)"/>
    <path d="M802 995 C805 980 815 975 830 978 C845 982 850 990 860 988 C900 980 950 960 985 985 C1010 965 1040 955 1075 960 C1130 960 1160 975 1165 1000 C1172 1050 1180 1120 1181 1200 H802 Z" fill="var(--blue)"/>
  </svg>

  <div class="abs step-num" style="left:43px;top:931px">1</div>
  <div class="abs step-num" style="left:552px;top:979px">2</div>
  <div class="abs step-num" style="left:1046px;top:931px">3</div>

  <div class="abs step-title" style="left:20px;width:380px;top:1048px">Research, Review, and<br>Evaluation Criteria</div>
  <ul class="abs step-list" style="left:56px;top:1128px">
    <li>District needs analysis</li>
    <li style="margin-top:20px">Program reviews and alignment to need</li>
  </ul>

  <div class="abs step-title" style="left:416px;width:366px;top:1082px">Cost / Benefit Analysis</div>
  <ul class="abs step-list" style="left:443px;top:1128px">
    <li>Cost alignment based on research,<br>review and evaluation of programs</li>
    <li style="margin-top:16px">Program cost by product offering</li>
  </ul>

  <div class="abs step-title" style="left:802px;width:380px;top:1047px">Education Survey<br>and Culture Scan</div>
  <ul class="abs step-list" style="left:826px;top:1128px">
    <li>District observation and perception survey</li>
    <li style="margin-top:19px">Culture scan to identify education best practices</li>
  </ul>

</div>
</body>
</html>
```